Website for data analytics startup

I have a landing page up at http://quenvo.io I need to expand this into a basic company website. I want something similar to this design: http://kelmarix.com/examples/carousel/

I need HTML and CSS for each of the designs, once they are approved. I need the following pages: home page, product, team, blog, and a design for the container of our demo application.

Our logo is attached and also available here: https://files.dravistore.net/quenvo.public/LOGO-colour.png I would like the website branding to match the logo.

I need a blog design with CSS that works with Tumblr.

Our app can be seen at http://demo.quenvo.io Please don't change the look of the network graph itself, only the surrounding content.

For CSS, I want you to use Bootstrap or Foundation as the starting point.

Target Market(s)

Sales and marketing, strategy

Industry/Entity Type

It Company

Coding

Coded - Design and coding required

Number of Pages Required

4 page

Font styles to use
Serif
Sans Serif

Requirements
Must have
• Clean, healthy appeal. Must work well with our logo. Blog page must integrate with Tumblr easily. Must use Bootstrap or Foundation for the starting point of the HTML/CSS.
Should not have
• Ugly crap, flash looking design. NO FLASH.

```html
<!DOCTYPE html>
<html lang="en">
<head>
<meta charset="utf-8">
<title>Quenvo — Home</title>
<link href="https://fonts.googleapis.com/css2?family=Arimo:wght@400;700&family=PT+Sans:wght@400;700&display=swap" rel="stylesheet">
<style>
  :root {
    --green: #66b12f;
    --blue: #3fa9dc;
    --blue-light: #5cbfe9;
    --navy: #0f4a66;
    --ink: #222222;
    --muted: #4a4a4a;
    --rule: #e4e4e4;
    --footer: #2b2b2b;
    --white: #ffffff;
    --hero-edge: #2a78c2;
    --hero-mid: #1d3a5c;
  }
  * { box-sizing: border-box; margin: 0; padding: 0; }
  html, body { width: 966px; height: 1200px; overflow: hidden; }
  body { position: relative; background: var(--white); font-family: "Arimo", Arial, sans-serif; color: var(--ink); }

  .site-header { position: absolute; top: 0; left: 0; width: 966px; height: 66px; background: var(--white); border-bottom: 1px solid #d8d8d8; }
  .brand { position: absolute; left: 62px; top: 20px; display: flex; align-items: center; gap: 6px; }
  .brand-dot { width: 9px; height: 9px; border-radius: 50%; background: var(--green); }
  .brand-name { font-weight: 700; font-size: 23px; color: var(--navy); letter-spacing: -0.3px; }
  .main-nav { position: absolute; top: 0; right: 0; height: 66px; display: flex; }
  .main-nav a { display: block; height: 66px; line-height: 84px; font-size: 12px; color: #333; text-decoration: none; padding: 0 15px; }
  .main-nav a.active { background: var(--green); color: var(--white); width: 61px; padding: 0; text-align: center; margin-right: 4px; }
  .main-nav a:last-child { margin-right: 48px; }

  .hero { position: absolute; top: 66px; left: 0; width: 966px; height: 420px; overflow: hidden; }
  .hero-image { position: absolute; inset: 0;
    background: radial-gradient(ellipse 520px 340px at 50% 55%, var(--hero-mid) 0%, #23507f 60%, var(--hero-edge) 100%); }
  .hero-title { position: absolute; left: 59px; margin: 0; font-weight: 400; font-size: 28px; }
  .hero-title span { display: inline-block; background: rgba(92,180,228,0.82); color: var(--white); font-weight: 400; font-size: 28px; line-height: 38px; padding: 0 16px; letter-spacing: 0.4px; }
  .hero-title.line-1 { top: 136px; }
  .hero-title.line-2 { top: 183px; }
  .hero-cta { position: absolute; left: 59px; top: 246px; width: 196px; height: 35px; background: var(--blue-light); color: #10293a; font-size: 12px; line-height: 35px; text-align: center; }
  .hero-dots { position: absolute; left: 446px; top: 384px; width: 74px; height: 20px; background: rgba(60,60,60,0.85); display: flex; justify-content: center; align-items: center; gap: 6px; }
  .hero-dots i { width: 8px; height: 8px; border-radius: 50%; background: var(--white); }
  .hero-dots i.current { background: var(--blue-light); }

  .get-started { position: absolute; top: 486px; left: 0; width: 966px; height: 223px; background: var(--green); text-align: center; }
  .get-started h2 { position: absolute; top: 38px; width: 100%; font-weight: 400; font-size: 27px; color: var(--white); letter-spacing: 0.4px; }
  .get-started p { position: absolute; top: 78px; width: 100%; font-size: 12.5px; color: #1f2a14; }
  .field { position: absolute; top: 112px; width: 195px; height: 32px; background: var(--white); font-size: 10.5px; color: #666; line-height: 32px; text-align: left; padding-left: 13px; border: 1px solid #e0e0e0; }
  .field.name { left: 59px; } .field.email { left: 277px; } .field.phone { left: 494px; } .field.message { left: 711px; }
  .callback { position: absolute; top: 164px; left: 398px; width: 170px; height: 34px; background: linear-gradient(#3a3a3a, #1d1d1d); color: var(--white); font-size: 12px; line-height: 34px; }
  .privacy { position: absolute; top: 175px; left: 583px; font-size: 10px; color: var(--white); }

  .about { position: absolute; top: 709px; left: 0; width: 966px; height: 419px; text-align: center; }
  .about h2 { position: absolute; top: 46px; width: 100%; font-family: "PT Sans", sans-serif; font-weight: 400; font-size: 28px; color: var(--ink); letter-spacing: 0.5px; }
  .about h2 em { font-style: normal; color: var(--blue); }
  .about .rule { position: absolute; top: 84px; left: 350px; width: 267px; height: 1px; background: var(--rule); }
  .about .rule b { position: absolute; left: 99px; top: -1px; width: 62px; height: 3px; background: var(--blue); }
  .about .intro { position: absolute; top: 108px; left: 74px; width: 818px; font-family: "PT Sans", sans-serif; font-size: 10px; line-height: 18px; color: var(--muted); }

  .feature { position: absolute; top: 193px; width: 270px; margin-left: -135px; text-align: center; }
  .feature.f1 { left: 193px; } .feature.f2 { left: 481px; } .feature.f3 { left: 768px; }
  .feature-icon { width: 68px; height: 68px; margin: 0 auto; border-radius: 50%; background: radial-gradient(circle at 40% 30%, #5cc2ee, #2f9fd8); display: flex; align-items: center; justify-content: center; }
  .feature h3 { margin-top: 22px; font-family: "PT Sans", sans-serif; font-weight: 400; font-size: 16px; color: var(--ink); }
  .feature p { margin-top: 13px; font-family: "PT Sans", sans-serif; font-size: 10px; line-height: 16px; color: var(--muted); padding: 0 6px; }
  .feature .more { display: inline-block; margin-top: 12px; width: 68px; height: 27px; background: linear-gradient(#5cc2ee, #35a2d9); color: #0f3b55; font-size: 11px; line-height: 27px; }

  .site-footer { position: absolute; top: 1128px; left: 0; width: 966px; height: 72px; background: var(--footer); }
  .site-footer .copy { position: absolute; left: 61px; top: 32px; font-size: 10.5px; color: var(--white); }
  .social { position: absolute; left: 778px; top: 28px; display: flex; gap: 4px; }
  .social span { width: 22px; height: 22px; border-radius: 50%; background: var(--white); }
</style>
</head>
<body>
  <header class="site-header">
    <div class="brand"><span class="brand-dot"></span><span class="brand-name">quenvo</span></div>
    <nav class="main-nav">
      <a class="active" href="#">Home</a>
      <a href="#">About Us</a>
      <a href="#">Services</a>
      <a href="#">Blog</a>
      <a href="#">Contact</a>
    </nav>
  </header>

  <section class="hero">
    <div class="hero-image" role="img" aria-label="Photo of a businessman touching a glowing network of connected people icons"></div>
    <h1 class="hero-title line-1"><span>Quenvo Maps Markets to Drive</span></h1>
    <div class="hero-title line-2"><span>Sales and Marketing</span></div>
    <div class="hero-cta">Sign up now for a free demo</div>
    <div class="hero-dots"><i class="current"></i><i></i><i></i><i></i></div>
  </section>

  <section class="get-started">
    <h2>Get Started Now</h2>
    <p>As soon as you contact our expert team, this will be the only form you have to fill in!</p>
    <div class="field name">Enter Name*</div>
    <div class="field email">Enter Email*</div>
    <div class="field phone">Phone Number</div>
    <div class="field message">Message</div>
    <div class="callback">Request A Call Back</div>
    <div class="privacy">100% Privacy Guaranteed..</div>
  </section>

  <section class="about">
    <h2>About <em>Quenvo</em></h2>
    <div class="rule"><b></b></div>
    <p class="intro">Sed ut perspiciatis unde omnis iste natus error sit voluptatem accusantium doloremque laudantium, totam rem aperiam, eaque ipsa quae ab illo inventore veritatis et quasi architecto beatae vitae dicta sunt explicabo. Nemo enim ipsam voluptatem quia voluptas sit aspernatur aut odit aut fugit, sed quia consequuntur magni dolores eos qui ratione voluptatem sequi nesciunt. Sed ut perspiciatis unde omnis iste natus error sit voluptatem accusantium doloremque</p>

    <div class="feature f1">
      <div class="feature-icon">
        <svg width="26" height="26" viewBox="0 0 26 26" fill="none" stroke="#fff" stroke-width="2">
          <rect x="3" y="5" width="20" height="18" rx="1"/><line x1="3" y1="10" x2="23" y2="10"/>
          <line x1="8" y1="2" x2="8" y2="7"/><line x1="18" y1="2" x2="18" y2="7"/>
          <line x1="3" y1="15" x2="23" y2="15" stroke-width="1"/><line x1="3" y1="19" x2="23" y2="19" stroke-width="1"/>
          <line x1="9" y1="10" x2="9" y2="23" stroke-width="1"/><line x1="13" y1="10" x2="13" y2="23" stroke-width="1"/><line x1="17" y1="10" x2="17" y2="23" stroke-width="1"/>
        </svg>
      </div>
      <h3>Voluptatem</h3>
      <p>Sed ut perspiciatis unde omnis iste natus error situd sit voluptatem accusantium doloremque.</p>
      <span class="more">More</span>
    </div>
    <div class="feature f2">
      <div class="feature-icon">
        <svg width="30" height="26" viewBox="0 0 30 26" fill="#fff">
          <ellipse cx="12" cy="10" rx="11" ry="8"/><path d="M5 15 L3 21 L10 17 Z"/>
          <ellipse cx="20" cy="15" rx="9" ry="6.5" stroke="#3aa6dc" stroke-width="1.5"/><path d="M25 19 L28 24 L21 21 Z"/>
        </svg>
      </div>
      <h3>Voluptatem</h3>
      <p>Sed ut perspiciatis unde omnis iste natus error situd sit voluptatem accusantium doloremque.</p>
      <span class="more">More</span>
    </div>
    <div class="feature f3">
      <div class="feature-icon">
        <svg width="28" height="28" viewBox="0 0 28 28" fill="#fff">
          <path d="M24 4 C17 4 12 8 9 13 L15 19 C20 16 24 11 24 4 Z"/>
          <path d="M9 13 L4 13 L8 9 L13 9 Z"/><path d="M15 19 L15 24 L19 20 L19 15 Z"/>
          <path d="M8 17 L11 20 L5 23 Z"/>
        </svg>
      </div>
      <h3>Voluptatem</h3>
      <p>Sed ut perspiciatis unde omnis iste natus error situd sit voluptatem accusantium doloremque.</p>
      <span class="more">More</span>
    </div>
  </section>

  <footer class="site-footer">
    <p class="copy">Copyright © 2015 Quenvo, Inc. All rights reserved.</p>
    <div class="social" aria-label="Social links"><span></span><span></span><span></span><span></span><span></span></div>
  </footer>
</body>
</html>
```